Business Card and Letterhead for Pimlu - modern real estate business

I need a double sided business card design for Pimlu. Please see business card brief here https://files.trelvonadocs.com/sheet/r/7QzTmWbaXLJnoPEd-kRyUgFhHsstbvCe2qfoMxDa_pz/view?mode=shared

Please feel free to design the business cards however you feel best. I am happy to give some creative freedoms and then provide feedback from there.

Please then also create a letterhead to match the business card design

Colors

Designer to choose colors to be used in the design.

Requirements
Must have
• Must be a modern, elegant business card which looks very professional

```html
<!DOCTYPE html>
<html lang="en">
<head>
<meta charset="utf-8">
<title>Pimlu Business Card</title>
<link href="https://fonts.googleapis.com/css2?family=Montserrat:wght@400;600;700&display=swap" rel="stylesheet">
<style>
  :root {
    --red: #e31e26;
    --black: #1e1d1d;
    --white: #ffffff;
    --paper: #f7f7f7;
    --text: #222222;
    --backdrop: #d6d8da;
  }
  * { margin: 0; padding: 0; box-sizing: border-box; }
  html, body { width: 1200px; height: 800px; overflow: hidden; }
  body {
    background: var(--backdrop);
    font-family: "Montserrat", sans-serif;
    position: relative;
  }
  .card {
    position: absolute;
    left: 290px;
    width: 620px;
    height: 354px;
    box-shadow: 0 6px 18px rgba(0,0,0,0.18);
    overflow: hidden;
  }
  .card-back { top: 28px; background: var(--black); }
  .card-front { top: 418px; background: linear-gradient(180deg, var(--white) 0%, var(--paper) 100%); }

  .back-wordmark {
    position: absolute; inset: 0;
    display: flex; align-items: center; justify-content: center;
    color: var(--red); font-weight: 600; font-size: 72px; letter-spacing: 6px;
  }

  .portrait-frame {
    position: absolute; left: 92px; top: 28px;
    width: 176px; height: 190px;
    border: 3px solid var(--red);
    background: var(--white);
    padding: 7px;
  }
  .portrait {
    width: 100%; height: 100%;
    background: linear-gradient(160deg, #9fb08a 0%, #5f6d52 45%, #2b2c30 100%);
  }
  .portrait-pointer {
    position: absolute; left: 168px; top: 218px;
    width: 0; height: 0;
    border-left: 12px solid transparent;
    border-right: 12px solid transparent;
    border-top: 12px solid var(--red);
  }
  .agent-name {
    position: absolute; left: 40px; width: 280px; top: 240px;
    text-align: center; color: var(--red);
    font-weight: 700; font-size: 19px; letter-spacing: 0.5px;
  }
  .agent-title {
    position: absolute; left: 40px; width: 280px; top: 266px;
    text-align: center; color: var(--text); font-size: 14px;
  }

  .base-band {
    position: absolute; left: 0; bottom: 0; width: 100%; height: 22px;
    background: var(--black);
  }
  .accent-block {
    position: absolute; left: 52px; bottom: 0; width: 262px; height: 34px;
    background: var(--red);
    border-left: 4px solid var(--white);
    border-right: 4px solid var(--white);
    border-top: 4px solid var(--white);
  }

  .front-wordmark {
    position: absolute; right: 62px; top: 66px;
    color: var(--red); font-weight: 600; font-size: 44px; letter-spacing: 4px;
  }

  .contact {
    position: absolute; right: 38px; top: 200px;
    text-align: right; color: var(--text); font-size: 15px; line-height: 1.3;
  }
  .address { margin-bottom: 10px; padding-right: 26px; }
  .contact-line { display: flex; align-items: center; justify-content: flex-end; gap: 10px; }
  .contact-line svg { width: 16px; height: 16px; flex: none; }
</style>
</head>
<body>
  <section class="card card-back">
    <div class="back-wordmark">PIMLU</div>
  </section>

  <section class="card card-front">
    <div class="portrait-frame">
      <div class="portrait" role="img" aria-label="Portrait photo of the agent outdoors"></div>
    </div>
    <div class="portrait-pointer"></div>
    <div class="agent-name">DANE MORROW</div>
    <div class="agent-title">Licenced Real Estate Agent</div>

    <div class="front-wordmark">PIMLU</div>

    <div class="contact">
      <div class="address">PO Box 6130<br>Larkfield NSW 2841</div>
      <div class="contact-line">0412 386 904
        <svg viewBox="0 0 16 16" aria-hidden="true"><path fill="#e31e26" d="M3.5 1.5l2.5 0 1 3.5-1.6 1.2a8 8 0 0 0 4.4 4.4L11 9l3.5 1v2.5a1.5 1.5 0 0 1-1.5 1.5A11.5 11.5 0 0 1 2 3a1.5 1.5 0 0 1 1.5-1.5z"/></svg>
      </div>
      <div class="contact-line">dane@pimlu.com
        <svg viewBox="0 0 16 16" aria-hidden="true"><rect x="1.5" y="3.5" width="13" height="9" fill="none" stroke="#e31e26" stroke-width="1.5"/><path d="M1.5 3.5l6.5 5 6.5-5" fill="none" stroke="#e31e26" stroke-width="1.5"/></svg>
      </div>
      <div class="contact-line">www.pimlu.com
        <svg viewBox="0 0 16 16" aria-hidden="true"><g fill="none" stroke="#e31e26" stroke-width="1.3"><circle cx="8" cy="8" r="6.5"/><ellipse cx="8" cy="8" rx="3" ry="6.5"/><path d="M1.5 8h13M2.5 5h11M2.5 11h11"/></g></svg>
      </div>
    </div>

    <div class="base-band"></div>
    <div class="accent-block"></div>
  </section>
</body>
</html>
```